High-end construction company needs a business card design

We need a modern looking business card that draws people in, is memorable and looks so good people will want to sick it on their fridges.
On the first side what is needed are:
Logo
My name - Tomasz Brelwik
Title - Managing Director
Website - www.varkelt.co.uk
Email - tomasz@varkelt.co.uk
Telephone - 020 5194 6281
Mobile - 07845139072
On the back side was is needed is a list of all the services we provide:
-Kitchen Renovations
-Bathroom Renovations
-House Renovations
-Garage Conversions
-Extensions
-Loft Conversions
-Conservatories
-Carpentry
-Tiling
-Electrical
-Plumbing & Heating
-Bricklaying
-Landscaping
-Decorating
-Plastering
We would like the colours to be the same shades as on the logo with grey or black for the words.
Target Market(s)
Anyone who needs building work done
Contact Information for Business Card
This business card is for a construction company which strives to deliver excellent service and quality.
The look and feel of the card should represent this.
Requirements
Must have
- On the first side what is needed are:
Logo
My name - Tomasz Brelwik
Title - Managing Director
Website - www.varkelt.co.uk
Email - tomasz@varkelt.co.uk
Telephone - 020 5194 6281
Mobile - 07845139072
Nice to have
- Cool looking features

```html
<!DOCTYPE html>
<html lang="en">
<head>
<meta charset="utf-8">
<title>Varkelt Construction Ltd – Business Card</title>
<link rel="stylesheet" href="https://fonts.googleapis.com/css2?family=Montserrat:wght@400;500;700&display=swap">
<style>
  :root {
    --page-bg: #e4e4e4;
    --brand-green: #4a8a3e;
    --brand-light: #6cb644;
    --card-white: #f4f4f4;
    --ink: #2b2b2b;
    --on-green: #ffffff;
  }
  * { margin: 0; padding: 0; box-sizing: border-box; }
  html, body { width: 1200px; height: 960px; overflow: hidden; }
  body {
    background: var(--page-bg);
    font-family: "Montserrat", Arial, sans-serif;
    position: relative;
  }
  .card {
    position: absolute;
    top: 193px;
    width: 360px;
    height: 555px;
    overflow: hidden;
  }
  .card--services { left: 221px; background: var(--brand-green); }
  .card--contact { left: 622px; background: var(--card-white); text-align: center; }

  .services-list {
    list-style: none;
    margin-top: 56px;
    text-align: center;
    color: var(--on-green);
    font-size: 15px;
    line-height: 27.7px;
    font-weight: 400;
  }
  .services-art {
    position: absolute;
    left: 0; bottom: 0;
    width: 360px; height: 245px;
    background: linear-gradient(160deg, rgba(108,182,68,0) 0%, rgba(108,182,68,0.75) 45%, rgba(240,240,240,0.55) 100%);
  }

  .brand {
    position: absolute;
    top: 58px; left: 0; right: 0;
    color: var(--brand-light);
    font-weight: 700;
    line-height: 1;
  }
  .brand__mark {
    display: block;
    margin: 0 auto 10px;
    width: 76px; height: 76px;
    border-radius: 50%;
    background: var(--brand-light);
  }
  .brand__name { font-size: 48px; letter-spacing: 1px; display: block; }
  .brand__sub { font-size: 13px; letter-spacing: 2.5px; display: block; margin-top: 6px; }

  .person { position: absolute; top: 320px; left: 0; right: 0; }
  .person__name { color: var(--brand-green); font-size: 18px; font-weight: 700; letter-spacing: 0.5px; line-height: 22px; }
  .person__title { color: var(--ink); font-size: 15px; font-weight: 500; line-height: 20px; margin-top: 1px; }

  .contact-icons {
    position: absolute; top: 401px; left: 0; right: 0;
    display: flex; justify-content: center; gap: 4px;
  }
  .contact-icons svg { width: 19px; height: 19px; }
  .contact-lines {
    position: absolute; top: 424px; left: 0; right: 0;
    list-style: none;
    color: var(--ink); font-size: 15px; line-height: 19.6px; font-weight: 500;
  }
</style>
</head>
<body>
  <section class="card card--services">
    <ul class="services-list">
      <li>Kitchen Renovations · Extensions</li>
      <li>Bathroom Renovations · Bricklaying</li>
      <li>House Renovations · Decorating</li>
      <li>Garage Conversions · Electrical</li>
      <li>Plumbing &amp; Heating · Plastering</li>
      <li>Loft Conversions · Landscaping</li>
      <li>Conservatories · Carpentry · Tiling</li>
    </ul>
    <div class="services-art" role="img" aria-label="Large illustration of an excavator arm over a house roof and city buildings"></div>
  </section>

  <section class="card card--contact">
    <div class="brand">
      <span class="brand__mark"></span>
      <span class="brand__name">VARKELT</span>
      <span class="brand__sub">CONSTRUCTION LTD</span>
    </div>

    <div class="person">
      <h1 class="person__name">TOMASZ BRELWIK</h1>
      <p class="person__title">Managing Director</p>
    </div>

    <div class="contact-icons" aria-hidden="true">
      <svg viewBox="0 0 20 20"><circle cx="10" cy="10" r="10" fill="#4a8a3e"/><path d="M6.5 5.5l2 0 1 2.5-1.3 1c.6 1.3 1.5 2.2 2.8 2.8l1-1.3 2.5 1v2c0 .5-.5 1-1 1C9.5 14.3 5.7 10.5 5.5 6.5c0-.5.5-1 1-1z" fill="#fff"/></svg>
      <svg viewBox="0 0 20 20"><circle cx="10" cy="10" r="10" fill="#4a8a3e"/><rect x="7" y="4.5" width="6" height="11" rx="1" fill="none" stroke="#fff" stroke-width="1.3"/><circle cx="10" cy="13.5" r=".7" fill="#fff"/></svg>
      <svg viewBox="0 0 20 20"><circle cx="10" cy="10" r="10" fill="#4a8a3e"/><rect x="5" y="6.5" width="10" height="7" fill="none" stroke="#fff" stroke-width="1.2"/><path d="M5 6.5l5 4 5-4" fill="none" stroke="#fff" stroke-width="1.2"/></svg>
      <svg viewBox="0 0 20 20"><circle cx="10" cy="10" r="10" fill="#4a8a3e"/><g fill="none" stroke="#fff" stroke-width="1.1"><circle cx="10" cy="10" r="5"/><ellipse cx="10" cy="10" rx="2.2" ry="5"/><path d="M5 10h10"/></g></svg>
    </div>

    <ul class="contact-lines">
      <li>020 5194 6281</li>
      <li>0784 513 9072</li>
      <li>tomasz@varkelt.co.uk</li>
      <li>www.varkelt.co.uk</li>
    </ul>
  </section>
</body>
</html>
```